Tandem Hearth Works Pty Ltd

We need business cards for a company based in Perth, we install, service and maintain fire equipment.
On the front we want a great design with our logo and a small spot for our full company name, general company email address and office number. On the back we need space for our name, title, mobile number and email address on the back.

Target Market(s)

Facility managers and commercial/industrial building owners/occupiers.

Contact Information for Business Card

Font styles to use
Sans Serif

Requirements
Must have
• Please only submit 5 of your best samples.
Darker tones are preferred.
Nice to have
• We want to use, black, red and grey. Keep it modern and clean.
I've attached the company logo and a sample of a boarder we use on our emergency plans.
Should not have
• No preference. Let the designer choose.

```html
<!DOCTYPE html>
<html lang="en">
<head>
<meta charset="utf-8">
<title>Tandem Hearth Works – Business Card</title>
<link rel="stylesheet" href="https://fonts.googleapis.com/css2?family=Arimo:wght@400;700&display=swap">
<style>
  :root {
    --card-red: #ed1c24;
    --ink-white: #ffffff;
    --window-grey: #e4dcdc;
    --window-grey-deep: #cfc4c4;
    --page-bg: #ecebea;
  }
  html, body {
    margin: 0;
    padding: 0;
    width: 1200px;
    height: 900px;
    overflow: hidden;
    background: var(--page-bg);
    font-family: "Arimo", Arial, sans-serif;
  }
  .card {
    position: absolute;
    left: 100px;
    top: 140px;
    width: 1000px;
    height: 619px;
    background: var(--card-red);
    color: var(--ink-white);
    overflow: hidden;
  }
  .person {
    position: absolute;
    left: 42px;
    top: 70px;
    z-index: 1;
  }
  .person-name {
    margin: 0;
    font-size: 38px;
    font-weight: 700;
    line-height: 1;
    letter-spacing: 0.2px;
  }
  .person-title {
    margin: 4px 0 0;
    font-size: 29px;
    font-weight: 400;
    line-height: 1.1;
  }
  .contact-list {
    list-style: none;
    margin: 0;
    padding: 0;
  }
  .contact-list li {
    display: flex;
    align-items: center;
    height: 36px;
    font-size: 28px;
    line-height: 1;
    white-space: nowrap;
  }
  .contact-list .icon {
    width: 26px;
    height: 26px;
    margin-right: 16px;
    flex: none;
    fill: var(--ink-white);
  }
  .person .contact-list { margin-top: 16px; }
  .company {
    position: absolute;
    left: 42px;
    top: 294px;
    z-index: 1;
  }
  .company-name {
    margin: 0;
    font-size: 40px;
    font-weight: 700;
    line-height: 45px;
    text-transform: uppercase;
  }
  .company-phone {
    margin: 14px 0 10px;
    font-size: 42px;
    font-weight: 700;
    line-height: 1;
  }
  .brand-window {
    position: absolute;
    left: 414px;
    top: 43px;
    width: 532px;
    height: 532px;
    border-radius: 50%;
    background: radial-gradient(circle at 45% 45%, var(--window-grey) 0%, var(--window-grey) 55%, var(--window-grey-deep) 100%);
    display: flex;
    align-items: center;
    justify-content: center;
  }
  .brand-name {
    margin: 0;
    color: var(--card-red);
    font-size: 56px;
    font-weight: 700;
    line-height: 62px;
    text-align: center;
    text-transform: uppercase;
  }
</style>
</head>
<body>
  <main class="card">
    <section class="person">
      <h1 class="person-name">OWEN PRITCHARD</h1>
      <p class="person-title">Managing Director</p>
      <ul class="contact-list">
        <li>
          <svg class="icon" viewBox="0 0 24 24" aria-hidden="true"><path d="M7 1h10a2 2 0 0 1 2 2v18a2 2 0 0 1-2 2H7a2 2 0 0 1-2-2V3a2 2 0 0 1 2-2zm0 3v14h10V4zm5 15.5a1.2 1.2 0 1 0 0 2.4 1.2 1.2 0 0 0 0-2.4z"/></svg>
          555.0142.0142
        </li>
        <li>
          <svg class="icon" viewBox="0 0 24 24" aria-hidden="true"><path d="M1 5h22v15H1zm2 2.2V18h18V7.2l-9 7zM3.8 7l8.2 6.4L20.2 7z"/></svg>
          name@tandemhearth.com
        </li>
      </ul>
    </section>

    <section class="company">
      <h2 class="company-name">Tandem Hearth<br>Works<br>Pty Ltd</h2>
      <p class="company-phone">555.0190.0190</p>
      <ul class="contact-list">
        <li>
          <svg class="icon" viewBox="0 0 24 24" aria-hidden="true"><path d="M1 5h22v15H1zm2 2.2V18h18V7.2l-9 7zM3.8 7l8.2 6.4L20.2 7z"/></svg>
          info@tandemhearth.com
        </li>
        <li>
          <svg class="icon" viewBox="0 0 24 24" aria-hidden="true"><path d="M12 1a11 11 0 1 0 0 22 11 11 0 0 0 0-22zm-1 2.1V7H7.6c.8-2.1 2-3.5 3.4-3.9zm2 0c1.4.4 2.6 1.8 3.4 3.9H13zM5.5 7H3.8a9 9 0 0 1 3.4-3 12 12 0 0 0-1.7 3zm12.9 0a12 12 0 0 0-1.7-3 9 9 0 0 1 3.5 3zM3.1 9h3a17 17 0 0 0-.1 2H3zm5 0H11v2H7.9c0-.7.1-1.4.2-2zm4.9 0h2.9l.2 2H13zm4.9 0h3a9 9 0 0 1 .2 2H18c0-.7 0-1.4-.1-2zM3 13h3l.1 2h-3A9 9 0 0 1 3 13zm4.9 0H11v2H8.1c-.1-.6-.2-1.3-.2-2zM13 13h3.1c0 .7-.1 1.4-.2 2H13zm5 0h3a9 9 0 0 1-.2 2h-3zM3.8 17h1.7a12 12 0 0 0 1.7 3 9 9 0 0 1-3.4-3zm3.8 0H11v3.9c-1.4-.4-2.6-1.8-3.4-3.9zM13 17h3.4c-.8 2.1-2 3.5-3.4 3.9zm5.5 0h1.7a9 9 0 0 1-3.4 3 12 12 0 0 0 1.7-3z"/></svg>
          www.tandemhearth.com
        </li>
      </ul>
    </section>

    <div class="brand-window">
      <p class="brand-name">Tandem<br>Hearth<br>Works</p>
    </div>
  </main>
</body>
</html>
```